Custom Woodworking and Rock Design

We specialize in original, high quality, wood and rock art. It’s should be self explanatory ask questions if you need. Your team designing a logo. Furniture is custom made to order. Rocks are designed depending on consumer needs. Wood and rock can also be combined for custom work. Painted rocks on vintage wood. Custom chairs and cabinets. Artistic rocks for multiple uses:garden, magnets, custom. All ideas and requests are welcome.

Target Market(s)

All

Contact Information for Business Card

Mara Voss
Talbertstonecraft@mailbrook.net

Font styles to use
Sans Serif

Requirements
Must have
• Clear lettering
Nice to have
• Eye catching
Should not have
• Blurr

```html
<!DOCTYPE html>
<html lang="en">
<head>
<meta charset="utf-8">
<title>Talbert Stonecraft – Business Card</title>
<link href="https://fonts.googleapis.com/css2?family=Open+Sans:wght@400;600;700&display=swap" rel="stylesheet">
<style>
  :root {
    --backdrop: #e9e7e4;
    --card-dark-top: #5d5d60;
    --card-dark-bottom: #3b3b3e;
    --card-light: #ffffff;
    --gold: #c9a46a;
    --ink: #4a4a4a;
    --muted: #5c5c5c;
  }
  * { margin: 0; padding: 0; box-sizing: border-box; }
  html, body {
    width: 1200px; height: 768px; overflow: hidden;
    background: var(--backdrop);
    font-family: "Open Sans", sans-serif;
  }
  .stage {
    width: 1200px; height: 768px;
    display: flex; align-items: center; justify-content: center; gap: 60px;
  }
  .card {
    width: 525px; height: 300px; position: relative;
    box-shadow: 0 6px 18px rgba(0,0,0,0.18);
  }
  .card--front {
    background: linear-gradient(160deg, var(--card-dark-top), var(--card-dark-bottom));
    display: flex; align-items: center; justify-content: center;
  }
  .brand {
    display: flex; align-items: center; gap: 12px;
    color: var(--gold); font-weight: 600; white-space: nowrap;
  }
  .brand__mark { width: 12px; height: 12px; border-radius: 50%; background: var(--gold); }
  .card--front .brand { font-size: 28px; }
  .card--back { background: var(--card-light); }
  .person { position: absolute; left: 34px; top: 44px; }
  .person__name {
    color: var(--gold); font-weight: 600; font-size: 19px;
    text-transform: uppercase; letter-spacing: 0.3px;
  }
  .person__role { color: var(--ink); font-size: 15px; margin-top: 2px; }
  .rule { position: absolute; height: 2px; background: var(--gold); }
  .rule--top { left: 96px; right: 34px; top: 91px; }
  .rule--bottom { left: 270px; right: 34px; bottom: 34px; }
  .contacts {
    position: absolute; left: 34px; top: 124px;
    list-style: none; color: var(--muted); font-size: 15px;
  }
  .contacts li { display: flex; align-items: center; gap: 9px; height: 27px; }
  .contacts svg { width: 17px; height: 17px; flex: none; }
  .card--back .brand {
    position: absolute; right: 34px; bottom: 48px; font-size: 18px; gap: 8px;
  }
  .card--back .brand__mark { width: 9px; height: 9px; }
</style>
</head>
<body>
<main class="stage">
  <section class="card card--front" aria-label="Card front">
    <div class="brand"><span class="brand__mark"></span><span>Talbert Stonecraft</span></div>
  </section>

  <section class="card card--back" aria-label="Card back">
    <div class="person">
      <p class="person__name">Mara Voss</p>
      <p class="person__role">Director</p>
    </div>
    <span class="rule rule--top"></span>

    <ul class="contacts">
      <li>
        <svg viewBox="0 0 20 20" aria-hidden="true"><path fill="#c9a46a" d="M3 7c0-2 2-3 7-3s7 1 7 3v1h-3V6.5H6V8H3zM5 9h10l1 7H4zm5 1.5a2.2 2.2 0 100 4.4 2.2 2.2 0 000-4.4z"/></svg>
        <span>555-014-2378</span>
      </li>
      <li>
        <svg viewBox="0 0 20 20" aria-hidden="true"><rect x="2" y="5" width="16" height="11" fill="#c9a46a"/><path d="M2 5l8 6 8-6" fill="none" stroke="#fff" stroke-width="1.5"/></svg>
        <span>Talbertstonecraft@mailbrook.net</span>
      </li>
      <li>
        <svg viewBox="0 0 20 20" aria-hidden="true"><rect x="2.5" y="3.5" width="15" height="11" fill="none" stroke="#c9a46a" stroke-width="1.6"/><circle cx="10" cy="9" r="3" fill="none" stroke="#c9a46a" stroke-width="1.4"/><path d="M6 17h8" stroke="#c9a46a" stroke-width="1.6"/></svg>
        <span>www.talbertstonecraft.net</span>
      </li>
    </ul>

    <div class="brand"><span class="brand__mark"></span><span>Talbert Stonecraft</span></div>
    <span class="rule rule--bottom"></span>
  </section>
</main>
</body>
</html>
```